Vorlanta PowerPoint Template

I have a company called Vorlanta, LLC and my company logo is already designed. I need a PowerPoint template that I will be using to pitch potential investors and business partners. This should be a very professional-looking template that leverages the company logo colors and really pops. The company is an AI product research and development company.

```html
<!DOCTYPE html>
<html lang="en">
<head>
<meta charset="utf-8">
<title>Vorlanta Pitch Template</title>
<link href="https://fonts.googleapis.com/css2?family=Red+Hat+Display:wght@400;500;600;700;800&display=swap" rel="stylesheet">
<style>
:root{
  --red:#c4252c;
  --red-bright:#e0262d;
  --ink:#454545;
  --ink-soft:#666;
  --gray-band:#4b4b4b;
  --canvas:#f2f2f3;
  --paper:#ffffff;
  --cover:#ebeaf0;
}
*{margin:0;padding:0;box-sizing:border-box}
html,body{width:1034px;height:1200px;overflow:hidden;background:var(--canvas);font-family:"Red Hat Display",Arial,sans-serif;color:var(--ink)}
.canvas{position:relative;width:1034px;height:1200px}
.slide{position:absolute;width:477px;height:268px;background:var(--paper);overflow:hidden}
.slide > *{position:absolute}
.col-a{left:27px}.col-b{left:530px}
.row-1{top:22px}.row-2{top:314px}.row-3{top:603px}.row-4{top:899px}

.title{left:14px;top:13px;font-size:18px;font-weight:800;letter-spacing:.2px;color:var(--ink)}
.title em{font-style:normal;color:var(--red)}
.title-rule{left:14px;top:38px;width:34px;height:2px;background:var(--red)}
.brand{display:flex;align-items:center;gap:5px;font-weight:700;color:var(--ink)}
.brand .dot{border-radius:50%;background:var(--red);flex:none}
.brand-top{right:14px;top:10px;font-size:21px}
.brand-top .dot{width:25px;height:25px}

.footer{left:6px;top:254px;width:471px;height:12px}
.footer .brand{position:absolute;left:0;top:-1px;font-size:12px;gap:4px}
.footer .brand .dot{width:12px;height:12px}
.band-red{position:absolute;left:70px;top:1px;width:164px;height:11px;background:var(--red);clip-path:polygon(0 0,100% 0,97% 100%,0 100%)}
.band-gray{position:absolute;left:232px;top:1px;width:239px;height:11px;background:var(--gray-band);clip-path:polygon(3% 0,100% 0,100% 100%,0 100%)}
.band-gray span{position:absolute;right:12px;top:1px;font-size:6.5px;color:#fff}

.photo{border-radius:9px}
.filler{font-size:5.6px;line-height:1.95;color:var(--ink-soft)}

/* cover */
.cover{background:linear-gradient(120deg,#eeedf2 0%,#e6e4ec 60%,#ebe9f0 100%)}
.cover-brand{left:18px;top:21px;font-size:40px;gap:10px}
.cover-brand .dot{width:46px;height:46px}
.cover-name{left:23px;top:107px;font-size:27px;font-weight:800;color:var(--red)}
.cover-tag{left:23px;top:153px;font-size:12.5px;font-weight:600;line-height:19px;color:#3e3e3e}
.cover-date{left:24px;top:240px;font-size:13px;font-weight:600;color:#3e3e3e}
.cover-visual{left:247px;top:25px;width:218px;height:218px;border-radius:50%;background:radial-gradient(circle at 50% 35%,#f2d68a 0,#4a9fc0 18%,#1c6a8c 45%,#0b3b55 100%)}

/* stats */
.stat{width:63px;height:32px;padding:4px 6px;border-radius:2px;box-shadow:0 1px 4px rgba(0,0,0,.15);background:#fff;color:var(--red)}
.stat b{display:block;font-size:12px;font-weight:500}
.stat small{font-size:5.6px}
.stat.filled{background:var(--red);color:#fff}

/* problem */
.headline{left:223px;top:48px;width:240px;font-size:14.5px;font-weight:500;line-height:20px;color:#3e3e3e}
.bullets{left:223px;top:121px;list-style:none;font-size:10px;color:#333}
.bullets li{height:22.5px;display:flex;align-items:center;gap:10px}
.bullets li::before{content:"";width:11px;height:11px;border-radius:50%;background:var(--red) radial-gradient(circle,#fff 0 1.6px,transparent 2px);flex:none}
.closing{left:223px;top:212px;width:240px;font-size:10px;line-height:14.5px;color:#333}

/* market */
.item-icon{width:27px;height:27px;border-radius:50%;background:var(--red);display:flex;align-items:center;justify-content:center}
.item-text{width:170px;font-size:5.8px;line-height:10px;color:#222}

/* vision */
.orb{width:94px;height:94px;border-radius:50%}
.orb-label{width:93px;height:29px;background:#fff;border-radius:4px;box-shadow:0 1px 5px rgba(0,0,0,.14);font-size:7.8px;line-height:11px;text-align:center;padding-top:4px;color:#222}

/* what we do */
.svc{font-size:10px;font-weight:700;color:#3e3e3e;line-height:16px}
.svc.left{text-align:right}
.svc-icon{width:34px;height:34px;border-radius:50%;display:flex;align-items:center;justify-content:center;box-shadow:0 1px 4px rgba(0,0,0,.2)}
.svc-icon.red{background:var(--red)}
.svc-icon.dark{background:#4a4a4a}
.hub{left:171px;top:68px;width:136px;height:136px;border-radius:50%;background:#fff;box-shadow:0 0 10px rgba(0,0,0,.15)}
.hub-core{left:180px;top:77px;width:118px;height:118px;border-radius:50%;background:var(--red)}

/* team */
.card{width:96px;height:154px;background:#fff;box-shadow:0 1px 6px rgba(0,0,0,.1);text-align:center}
.avatar{display:block;width:37px;height:37px;border-radius:50%;margin:13px auto 0;background:linear-gradient(160deg,#8b7a6e,#2f3338)}
.card h3{margin-top:10px;font-size:7.6px;font-weight:800;color:#111}
.card .role{font-size:6.2px;margin-top:3px;color:#222}
.card p{font-size:5.6px;line-height:10px;color:#888;margin:5px 5px 0;height:32px}
.socials{display:flex;justify-content:center;gap:3px;margin-top:6px}
.socials span{width:10px;height:10px;border-radius:50%;border:.8px solid #bbb}
.socials span.on{background:#3a3a3a;border-color:#3a3a3a}
.socials span.on.alt{background:var(--red);border-color:var(--red)}

/* closing */
.closing-slide{background:#4a4a4a}
.closing-bg{left:0;top:0;width:477px;height:268px;background:linear-gradient(110deg,#3d3d3d 0%,#555 45%,#474747 100%)}
.closing-brand{left:78px;top:50px;font-size:58px;font-weight:700;color:#fff;gap:16px}
.closing-brand .dot{width:70px;height:70px;background:var(--red);border:2px solid #fff}
.contact{display:flex;gap:7px;color:#fff}
.contact .pin{width:20px;height:20px;border-radius:50%;background:var(--red);flex:none;display:flex;align-items:center;justify-content:center;margin-top:0}
.contact b{display:block;font-size:8.5px;font-weight:800}
.contact span{display:block;font-size:6.8px;margin-top:5px;color:#eee}
.thanks{left:0;width:477px;top:186px;text-align:center;font-size:22px;font-weight:800;color:#fff}
</style>
</head>
<body>
<main class="canvas">

  <!-- Cover -->
  <section class="slide cover col-a row-1">
    <div class="brand cover-brand"><span class="dot"></span>Vorlanta</div>
    <h1 class="cover-name">Vorlanta, LLC</h1>
    <p class="cover-tag">AI Product Research &amp; Development<br>Empowering the Next Generation<br>of Intelligent Solutions</p>
    <p class="cover-date">May 2024</p>
    <div class="cover-visual" role="img" aria-label="Glowing light bulb held by a robotic hand on a deep blue network background"></div>
  </section>

  <!-- About -->
  <section class="slide col-b row-1">
    <h2 class="title">ABOUT <em>US</em></h2>
    <div class="title-rule"></div>
    <div class="brand brand-top"><span class="dot"></span>Vorlanta</div>
    <div class="photo" role="img" aria-label="Smiling businesswoman in a meeting with colleagues" style="left:16px;top:56px;width:161px;height:85px;background:linear-gradient(120deg,#2b2f36,#a68e78 50%,#3b3d44)"></div>
    <div class="photo" role="img" aria-label="Team meeting around a table in a bright glass office" style="left:16px;top:150px;width:166px;height:87px;background:linear-gradient(100deg,#3a3d3a,#d6d8d6 40%,#c9cccd 60%,#474a48)"></div>
    <p class="filler" style="left:206px;top:57px;width:252px">We study real user needs, test early ideas with data, and turn promising AI concepts into working products. Our mixed teams of researchers, engineers and designers move each idea from first question to a tested build, cutting risk and time at every step along the way for the partners we serve.</p>
    <p class="filler" style="left:205px;top:151px;width:252px">Founded to close the gap between research and market, we help partners ship AI that people actually use.</p>
    <div class="stat" style="left:210px;top:204px"><b>+1055</b><small>Happy Costumer</small></div>
    <div class="stat filled" style="left:284px;top:204px"><b>+78</b><small>Custumer Daily</small></div>
    <div class="footer"><div class="brand"><span class="dot"></span>Vorlanta</div><div class="band-red"></div><div class="band-gray"><span>Page No: 02</span></div></div>
  </section>

  <!-- Problem -->
  <section class="slide col-a row-2">
    <h2 class="title">THE <em>PROBLEM</em></h2>
    <div class="title-rule"></div>
    <div class="brand brand-top"><span class="dot"></span>Vorlanta</div>
    <svg style="left:0;top:0" width="220" height="268" viewBox="0 0 220 268" aria-hidden="true">
      <path d="M97 47 A96 96 0 0 1 97 239 L97 224 A81 81 0 0 0 97 62 Z" fill="var(--red)"/>
    </svg>
    <div role="img" aria-label="Team of engineers working at laptops in a modern office" style="left:14px;top:63px;width:162px;height:162px;border-radius:50%;background:linear-gradient(130deg,#1e2a3a,#6b7d8f 45%,#c8b09a 70%,#2a2e36)"></div>
    <p class="headline">Innovative Ai Product Ideas Often Face A Long And Inefficient Path To Market</p>
    <ul class="bullets">
      <li>Lack of clear research validation</li>
      <li>Fragmented development process</li>
      <li>Limited access to interdisciplinary AI expertise</li>
      <li>Poor product-market alignment</li>
    </ul>
    <p class="closing">The current AI development cycle is slow, costly, and risky.</p>
    <div class="footer"><div class="brand"><span class="dot"></span>Vorlanta</div><div class="band-red"></div><div class="band-gray"><span>Page No: 03</span></div></div>
  </section>

  <!-- Market -->
  <section class="slide col-b row-2">
    <h2 class="title">THE MARKET <em>OPPORTUNITY</em></h2>
    <div class="title-rule"></div>
    <div class="brand brand-top"><span class="dot"></span>Vorlanta</div>
    <div class="item-icon" style="left:18px;top:77px"><svg width="15" height="15" viewBox="0 0 16 16" fill="none" stroke="#fff" stroke-width="1.2"><circle cx="9" cy="5" r="3.5"/><path d="M1 12h4l3 1.5 6-3"/></svg></div>
    <p class="item-text" style="left:53px;top:76px">Demand for applied AI tools is rising across sectors, and buyers want proven, tested products fast.</p>
    <div class="item-icon" style="left:18px;top:128px"><svg width="15" height="15" viewBox="0 0 16 16" fill="none" stroke="#fff" stroke-width="1.2"><path d="M2 8l3-3 3 2 3-2 3 3-3 3-3-2-3 2z"/></svg></div>
    <p class="item-text" style="left:53px;top:128px">Firms lack in-house research teams and seek partners who can validate ideas before large spend.</p>
    <div class="item-icon" style="left:18px;top:180px"><svg width="15" height="15" viewBox="0 0 16 16" fill="none" stroke="#fff" stroke-width="1.2"><circle cx="8" cy="8" r="6"/><path d="M4 9l3-2 2 2 3-2"/></svg></div>
    <p class="item-text" style="left:53px;top:179px">Early movers that pair research with rapid builds gain lasting share in new AI markets.</p>
    <div class="photo" role="img" aria-label="Two businessmen reviewing documents at a table" style="left:242px;top:54px;width:101px;height:133px;background:linear-gradient(150deg,#5b5550,#b9a899 50%,#7b6f66)"></div>
    <div class="photo" role="img" aria-label="Two businessmen in suits looking at a laptop" style="left:356px;top:100px;width:101px;height:133px;background:linear-gradient(150deg,#2d3f5e,#8c9cb0 50%,#d8dde4)"></div>
    <div class="footer"><div class="brand"><span class="dot"></span>Vorlanta</div><div class="band-red"></div><div class="band-gray"><span>Page No: 04</span></div></div>
  </section>

  <!-- Vision -->
  <section class="slide col-a row-3">
    <h2 class="title">FROM VISION TO <em>VIABLE AI</em></h2>
    <div class="title-rule"></div>
    <div class="brand brand-top"><span class="dot"></span>Vorlanta</div>
    <div class="orb" role="img" aria-label="Hand touching a digital research and development interface" style="left:22px;top:66px;background:radial-gradient(circle at 50% 45%,#3a7f96,#0e2f40)"></div>
    <div class="orb-label" style="left:23px;top:142px">End-to-End R&amp;D<br>Services</div>
    <div class="orb" role="img" aria-label="Digital head profile made of circuitry" style="left:136px;top:108px;background:radial-gradient(circle at 50% 45%,#2f6fb0,#0b1c3a)"></div>
    <div class="orb-label" style="left:137px;top:192px">Cross-Functional<br>AI Expertise</div>
    <div class="orb" role="img" aria-label="Scientists working in a laboratory" style="left:251px;top:55px;background:radial-gradient(circle at 50% 45%,#9bbbd8,#1e4a78)"></div>
    <div class="orb-label" style="left:252px;top:142px">Data-Driven<br>Prototyping &amp; Testing</div>
    <div class="orb" role="img" aria-label="Rocket launching above a rising growth chart" style="left:367px;top:108px;background:radial-gradient(circle at 50% 45%,#c98a4a,#1b3048 60%)"></div>
    <div class="orb-label" style="left:362px;top:192px;width:104px">Accelerated<br>Go-to-Market Strategies</div>
    <div class="footer"><div class="brand"><span class="dot"></span>Vorlanta</div><div class="band-red"></div><div class="band-gray"><span>Page No: 05</span></div></div>
  </section>

  <!-- What we do -->
  <section class="slide col-b row-3">
    <h2 class="title">WHAT <em>WE DO</em></h2>
    <div class="title-rule"></div>
    <div class="brand brand-top"><span class="dot"></span>Vorlanta</div>
    <div class="hub"></div>
    <div class="hub-core"></div>

    <p class="svc left" style="right:331px;top:54px">AI Product Incubation</p>
    <div class="svc-icon red" style="left:144px;top:46px"><svg width="16" height="16" viewBox="0 0 16 16" fill="none" stroke="#fff" stroke-width="1.1"><path d="M4 14h8M5 11h6l1-6a4 4 0 0 0-8 0z"/><circle cx="8" cy="6" r="1.5"/></svg></div>
    <p class="svc left" style="right:357px;top:103px">Custom AI Prototypes</p>
    <div class="svc-icon red" style="left:119px;top:95px"><svg width="16" height="16" viewBox="0 0 16 16" fill="none" stroke="#fff" stroke-width="1.1"><rect x="4" y="4" width="8" height="7"/><path d="M6 11v3M10 11v3M8 1v3M2 7h2M12 7h2"/></svg></div>
    <p class="svc left" style="right:357px;top:141px">Research Validation<br>Report</p>
    <div class="svc-icon red" style="left:119px;top:143px"><svg width="16" height="16" viewBox="0 0 16 16" fill="none" stroke="#fff" stroke-width="1.1"><rect x="2" y="3" width="10" height="8"/><circle cx="11" cy="9" r="2.5"/><path d="M13 11l2 2"/></svg></div>
    <p class="svc left" style="right:333px;top:190px">Tech Stack Architecture<br>&amp; Integration</p>
    <div class="svc-icon red" style="left:144px;top:192px"><svg width="16" height="16" viewBox="0 0 16 16" fill="none" stroke="#fff" stroke-width="1.1"><circle cx="6" cy="5" r="2.5"/><path d="M2 14c0-3 2-5 4-5s4 2 4 5M10 9h4v5h-4"/></svg></div>

    <div class="svc-icon dark" style="left:296px;top:46px"><svg width="16" height="16" viewBox="0 0 16 16" fill="none" stroke="#fff" stroke-width="1.1"><path d="M8 13S2 9 2 5.5A3 3 0 0 1 8 4a3 3 0 0 1 6 1.5C14 9 8 13 8 13z"/><path d="M4 8h2l1-2 2 4 1-2h2"/></svg></div>
    <p class="svc" style="left:339px;top:54px">Healthcare</p>
    <div class="svc-icon dark" style="left:320px;top:95px"><svg width="16" height="16" viewBox="0 0 16 16" fill="none" stroke="#fff" stroke-width="1.1"><rect x="2" y="3" width="9" height="10"/><path d="M5 6h3M5 9h3"/><circle cx="12" cy="11" r="2.5"/></svg></div>
    <p class="svc" style="left:361px;top:103px">Fintech</p>
    <div class="svc-icon dark" style="left:320px;top:143px"><svg width="16" height="16" viewBox="0 0 16 16" fill="none" stroke="#fff" stroke-width="1.1"><circle cx="8" cy="8" r="3"/><path d="M8 1v3M8 12v3M1 8h3M12 8h3M3 3l2 2M11 11l2 2M13 3l-2 2M3 13l2-2"/></svg></div>
    <p class="svc" style="left:361px;top:151px">Enterprise SaaS</p>
    <div class="svc-icon dark" style="left:296px;top:192px"><svg width="16" height="16" viewBox="0 0 16 16" fill="none" stroke="#fff" stroke-width="1.1"><path d="M3 14h8M6 14V9l4-4 3 2"/><circle cx="6" cy="9" r="1.2"/><circle cx="10" cy="5" r="1.2"/></svg></div>
    <p class="svc" style="left:339px;top:200px">Robotics &amp; IoT</p>
    <div class="footer"><div class="brand"><span class="dot"></span>Vorlanta</div><div class="band-red"></div><div class="band-gray"><span>Page No: 06</span></div></div>
  </section>

  <!-- Team -->
  <section class="slide col-a row-4">
    <h2 class="title"><span>OUR</span> <em>TEAM</em></h2>
    <div class="title-rule"></div>
    <div class="brand brand-top"><span class="dot"></span>Vorlanta</div>
    <article class="card" style="left:25px;top:63px">
      <span class="avatar" role="img" aria-label="Portrait of Marco Ellis"></span>
      <h3>MARCO ELLIS</h3><div class="role">Founder</div>
      <p>Leads strategy and research, guiding each product from idea to launch.</p>
      <div class="socials"><span class="on"></span><span></span><span></span></div>
    </article>
    <article class="card" style="left:135px;top:63px">
      <span class="avatar" role="img" aria-label="Portrait of Theo Brandt"></span>
      <h3>THEO BRANDT</h3><div class="role">Founder</div>
      <p>Heads engineering and builds the core systems behind every prototype.</p>
      <div class="socials"><span class="on alt"></span><span></span><span></span></div>
    </article>
    <article class="card" style="left:245px;top:63px">
      <span class="avatar" role="img" aria-label="Portrait of Priya Nolan"></span>
      <h3>PRIYA NOLAN</h3><div class="role">Founder</div>
      <p>Runs user research and makes sure each build meets a real need.</p>
      <div class="socials"><span class="on"></span><span></span><span></span></div>
    </article>
    <article class="card" style="left:356px;top:63px">
      <span class="avatar" role="img" aria-label="Portrait of Theo Brandt"></span>
      <h3>THEO BRANDT</h3><div class="role">Founder</div>
      <p>Drives partnerships and go-to-market plans for new AI products.</p>
      <div class="socials"><span class="on"></span><span></span><span></span></div>
    </article>
    <div class="footer"><div class="brand"><span class="dot"></span>Vorlanta</div><div class="band-red"></div><div class="band-gray"><span>Page No: 07</span></div></div>
  </section>

  <!-- Closing -->
  <section class="slide closing-slide col-b row-4" style="left:531px;top:897px">
    <div class="closing-bg" role="img" aria-label="Dimmed office scene with people at work"></div>
    <div class="brand closing-brand"><span class="dot"></span>Vorlanta</div>
    <div class="contact" style="left:24px;top:142px">
      <div class="pin"><svg width="9" height="11" viewBox="0 0 10 12"><path d="M5 0a4 4 0 0 0-4 4c0 3 4 8 4 8s4-5 4-8a4 4 0 0 0-4-4z" fill="#fff"/><circle cx="5" cy="4" r="1.5" fill="var(--red)"/></svg></div>
      <div><b>LOCATION:</b><span>Harbor Point Offices, United States</span></div>
    </div>
    <div class="contact" style="left:193px;top:142px">
      <div class="pin"><svg width="10" height="8" viewBox="0 0 10 8"><rect width="10" height="8" rx="1" fill="#fff"/><path d="M0 1l5 3.5L10 1" stroke="var(--red)" fill="none"/></svg></div>
      <div><b>EMAIL US:</b><span>info@vorlanta.com</span></div>
    </div>
    <div class="contact" style="left:356px;top:141px">
      <div class="pin"><svg width="10" height="10" viewBox="0 0 10 10"><path d="M2 0l2 2.5-1 1.5a6 6 0 0 0 3 3l1.5-1L10 8l-1.5 2C4 10 0 6 0 1.5z" fill="#fff"/></svg></div>
      <div><b>PHONE NUMBER:</b><span>+1 555 010 4420</span></div>
    </div>
    <p class="thanks">THANK YOU</p>
  </section>

</main>
</body>
</html>
```